Clear Cable Record Format Sticker

We need a set of stickers (~5-7cm) to promote the Clear Cable Record Format. Most of the people we will be handing these out to are technically minded (network operators, open-source coders, Internet standards folk, Internet measurement researchers). The design should include the CCRF icon and colour scheme (see here https://ccrf-sample.example/en/resources/).

network operators, open-source coders, Internet standards folk, Internet measurement researchers

• Hind

```html
<!DOCTYPE html>
<html lang="en">
<head>
<meta charset="utf-8">
<title>Clear Cable Record Format Sticker</title>
<link rel="stylesheet" href="https://fonts.googleapis.com/css2?family=Poppins:wght@500;600&family=Roboto+Condensed:wght@400&family=Montserrat:wght@700&display=swap">
<style>
  :root {
    --backdrop: #e9e6e1;
    --card-navy: #13142a;
    --lime: #b5cf3a;
    --white: #ffffff;
    --icon-shade: #1d1f3a;
  }
  html, body {
    margin: 0;
    padding: 0;
    width: 1200px;
    height: 1002px;
    overflow: hidden;
    background: var(--backdrop);
  }
  .canvas {
    position: relative;
    width: 1200px;
    height: 1002px;
  }
  .sticker {
    position: absolute;
    left: 75px;
    top: 126px;
    width: 1050px;
    height: 750px;
    background: var(--card-navy);
    border-radius: 26px;
    overflow: hidden;
  }
  .sticker-frame {
    position: absolute;
    inset: 10px;
    border: 2px solid var(--lime);
    border-radius: 22px;
  }
  .brand-name {
    position: absolute;
    left: 40px;
    top: 40px;
    margin: 0;
    font-family: "Poppins", sans-serif;
    font-weight: 600;
    font-size: 196px;
    line-height: 1;
    letter-spacing: 4px;
    color: var(--white);
  }
  .tagline {
    position: absolute;
    left: 41px;
    top: 322px;
    margin: 0;
    font-family: "Roboto Condensed", sans-serif;
    font-weight: 400;
    font-size: 34px;
    color: var(--lime);
  }
  .values {
    position: absolute;
    left: 41px;
    top: 424px;
    margin: 0;
    padding: 0;
    list-style: none;
    font-family: "Poppins", sans-serif;
    font-weight: 500;
    font-size: 39px;
    line-height: 64px;
    color: var(--white);
  }
  .web-address {
    position: absolute;
    left: 41px;
    top: 672px;
    margin: 0;
    font-family: "Montserrat", sans-serif;
    font-weight: 700;
    font-size: 31px;
    color: var(--lime);
  }
  .icon-area {
    position: absolute;
    left: 673px;
    top: 273px;
    width: 362px;
    height: 465px;
    border-radius: 16px;
    background: linear-gradient(160deg, var(--icon-shade), var(--card-navy));
  }
</style>
</head>
<body>
<div class="canvas">
  <div class="sticker">
    <div class="sticker-frame"></div>
    <h1 class="brand-name">CCRF</h1>
    <p class="tagline">Mapping The World,s Internet Backdone</p>
    <ul class="values">
      <li>Open Data.</li>
      <li>Stronger Networks.</li>
      <li>Connected World.</li>
    </ul>
    <p class="web-address">www.ccrf-sample.example</p>
    <div class="icon-area" role="img" aria-label="Place for the Clear Cable Record Format network icon in lime green"></div>
  </div>
</div>
</body>
</html>
```